Heron Haulage needs Bussiness cards!

Our new trucking company needs business cards!
We need the same design with two different names and emails, everything else it's the same.
I have included our original logo so we can use it for the design.
Note: the logo to be used is the o e with the buffalo on the right side, next to the letters H and H.

Target Market(s)

Trucking, refrigerated transportation, freight

Industry/Entity Type

Business

Contact Information for Business Card

Card #1:
Marcus Whitfield
marcuswhitfield@heronhaulage.example
1-855-317-6094
(555)238-7160
4117 W. Larkin Ave.
Alder Creek, TX 78590
www.heronhaulage.example

Card#2:
Rosalba Quintero
rosalba@heronhaulage.example
1-855-317-6094
(555)238-7160
4117 W. Larkin Ave.
Alder Creek, TX 78590
www.heronhaulage.example

Font styles to use
Sans Serif

Colors
0655a3
ec1f27
ffffff

Requirements
Must have
• our logo
Nice to have
• roads on background,

```html
<!DOCTYPE html>
<html lang="en">
<head>
<meta charset="utf-8">
<title>Heron Haulage – Business Cards</title>
<link href="https://fonts.googleapis.com/css2?family=Roboto:wght@400;500;900&display=swap" rel="stylesheet">
<style>
  :root {
    --navy: #0a3d73;
    --navy-deep: #072c55;
    --red: #ec1f27;
    --white: #ffffff;
    --stage: #e9ecf0;
    --muted: #dbe5f1;
  }
  * { box-sizing: border-box; margin: 0; padding: 0; }
  html, body { width: 1200px; height: 950px; overflow: hidden; }
  body {
    background: var(--stage);
    font-family: "Roboto", Arial, sans-serif;
    position: relative;
  }
  .card {
    position: absolute;
    left: 250px;
    width: 700px;
    height: 400px;
    border-radius: 4px;
    overflow: hidden;
    box-shadow: 0 12px 30px rgba(0,0,0,.18);
  }
  /* Back of card */
  .card--back {
    top: 50px;
    background: linear-gradient(160deg, var(--navy) 0%, var(--navy-deep) 100%);
    color: var(--white);
  }
  .wordmark {
    display: flex;
    align-items: center;
    gap: 14px;
    font-weight: 900;
    font-size: 50px;
    letter-spacing: -0.5px;
    line-height: 1;
    white-space: nowrap;
  }
  .wordmark__dot {
    width: 34px; height: 34px; border-radius: 50%;
    flex: none;
  }
  .card--back .wordmark {
    position: absolute; left: 0; right: 0; top: 145px;
    justify-content: center; color: var(--white);
  }
  .card--back .wordmark__dot { background: var(--white); }
  .card--back .web {
    position: absolute; left: 0; right: 0; top: 250px;
    text-align: center; font-size: 15px; letter-spacing: 5px;
    color: var(--muted);
  }
  /* Front of card */
  .card--front { top: 500px; background: var(--white); }
  .card__bands { position: absolute; inset: 0; }
  .card--front .wordmark {
    position: absolute; left: 0; right: 0; top: 100px;
    justify-content: center; color: var(--navy);
  }
  .card--front .wordmark__dot { background: var(--red); }
  .holder {
    position: absolute; right: 28px; top: 222px;
    text-align: right; color: var(--white);
    white-space: nowrap;
  }
  .holder__name { font-size: 22px; font-weight: 500; margin-bottom: 6px; }
  .holder__line { font-size: 13px; line-height: 1.6; color: var(--muted); }
  .contacts {
    position: absolute; left: 30px; top: 316px;
    list-style: none; color: var(--white); font-size: 14px;
  }
  .contacts li { display: flex; align-items: center; gap: 10px; height: 24px; }
  .contacts svg { width: 14px; height: 14px; flex: none; }
</style>
</head>
<body>

<section class="card card--back" aria-label="Business card back">
  <div class="wordmark"><span class="wordmark__dot"></span>Heron Haulage</div>
  <p class="web">www.heronhaulage.example</p>
</section>

<section class="card card--front" aria-label="Business card front">
  <svg class="card__bands" viewBox="0 0 700 400" preserveAspectRatio="none" aria-hidden="true">
    <rect x="0" y="0" width="700" height="10" fill="var(--red)"/>
    <rect x="0" y="14" width="700" height="2" fill="var(--red)"/>
    <polygon points="0,298 392,298 436,202 580,202 592,186 604,202 700,202 700,400 0,400" fill="var(--red)"/>
    <polygon points="0,303 395,303 439,207 582,207 592,194 602,207 700,207 700,400 0,400" fill="var(--navy)"/>
  </svg>

  <div class="wordmark"><span class="wordmark__dot"></span>Heron Haulage</div>

  <div class="holder">
    <p class="holder__name">Marcus Whitfield</p>
    <p class="holder__line">marcuswhitfield@heronhaulage.example</p>
    <p class="holder__line">4117 W. Larkin Ave. Alder Creek, TX 78590</p>
  </div>

  <ul class="contacts">
    <li>
      <svg viewBox="0 0 16 16"><path fill="var(--white)" d="M3 1h3l1 4-2 1c1 2 3 4 5 5l1-2 4 1v3c0 1-1 2-2 2C7 15 1 9 1 3c0-1 1-2 2-2z"/></svg>
      1-855-317-6094
    </li>
    <li>
      <svg viewBox="0 0 16 16"><rect x="4" y="1" width="8" height="14" rx="1.5" fill="none" stroke="var(--white)" stroke-width="1.5"/><circle cx="8" cy="12.5" r="0.9" fill="var(--white)"/></svg>
      (555)238-7160
    </li>
    <li>
      <svg viewBox="0 0 16 16"><circle cx="8" cy="8" r="6.5" fill="var(--white)"/><path d="M4.5 8h7M8 4.5v7" stroke="var(--navy)" stroke-width="1.2"/></svg>
      www.heronhaulage.example
    </li>
  </ul>
</section>

</body>
</html>
```